Oil and Gas Exploration and Production company needs a business card design

We need a business card design using our logo and colors in the logo. We want a mainstream design.

```html
<!DOCTYPE html>
<html lang="en">
<head>
<meta charset="UTF-8">
<title>Tavera Energy – Business Card</title>
<link rel="stylesheet" href="https://fonts.googleapis.com/css2?family=EB+Garamond:wght@400;700&display=swap">
<style>
  :root {
    --backdrop: #e9e9e9;
    --card-light: #fafafa;
    --card-dark: #070707;
    --ink: #111111;
    --gold: #e0a526;
    --logo-gold: #c99a2e;
    --white: #ffffff;
  }
  * { margin: 0; padding: 0; box-sizing: border-box; }
  html, body {
    width: 1200px;
    height: 586px;
    overflow: hidden;
    background: var(--backdrop);
  }
  .card {
    position: absolute;
    left: 150px;
    top: 23px;
    width: 900px;
    height: 540px;
    display: flex;
    font-family: "EB Garamond", Georgia, serif;
  }
  .card-front {
    width: 438px;
    height: 100%;
    background: var(--card-light);
    display: flex;
    align-items: center;
    justify-content: center;
  }
  .divider {
    width: 16px;
    height: 100%;
    background: linear-gradient(to right,
      var(--card-dark) 0 4px, var(--white) 4px 8px,
      var(--card-dark) 8px 12px, var(--white) 12px 16px);
  }
  .card-back {
    flex: 1;
    height: 100%;
    background: var(--card-dark);
    position: relative;
  }
  .brand {
    display: flex;
    align-items: center;
    gap: 14px;
  }
  .brand-dot {
    width: 30px;
    height: 30px;
    border-radius: 50%;
    background: var(--logo-gold);
  }
  .brand-name {
    font-size: 46px;
    font-weight: 700;
    color: var(--ink);
    letter-spacing: 0.5px;
  }
  .contact {
    position: absolute;
    left: 42px;
    top: 170px;
    color: var(--white);
  }
  .contact-name {
    font-size: 22px;
    font-weight: 700;
    color: var(--gold);
    line-height: 1.2;
  }
  .contact-role {
    font-size: 18px;
    line-height: 1.3;
  }
  .contact-address {
    margin-top: 22px;
    font-size: 20px;
    font-weight: 700;
    color: var(--gold);
  }
  .contact-list {
    list-style: none;
    margin-top: 28px;
  }
  .contact-list li {
    display: flex;
    align-items: center;
    height: 37px;
    font-size: 20px;
  }
  .contact-icon {
    width: 20px;
    height: 16px;
    margin-left: 11px;
    margin-right: 15px;
    fill: var(--gold);
  }
</style>
</head>
<body>
  <div class="card">
    <section class="card-front">
      <div class="brand">
        <span class="brand-dot"></span>
        <span class="brand-name">Tavera Energy</span>
      </div>
    </section>
    <div class="divider"></div>
    <section class="card-back">
      <div class="contact">
        <p class="contact-name">Dana Whitfield</p>
        <p class="contact-role">Chief Executive Officer</p>
        <p class="contact-address">4150 Harlow Pkwy, Suite 210, NC 27601</p>
        <ul class="contact-list">
          <li>
            <svg class="contact-icon" viewBox="0 0 20 16" aria-label="Phone">
              <path d="M1 5 Q10 -1 19 5 L17 7 L14 5.5 L14 4 Q10 3 6 4 L6 5.5 L3 7 Z"/>
              <path d="M5 7 L15 7 L18 15 L2 15 Z"/>
            </svg>
            <span>919.555.0142</span>
          </li>
          <li>
            <svg class="contact-icon" viewBox="0 0 20 16" aria-label="Fax">
              <rect x="5" y="1" width="10" height="4"/>
              <rect x="1" y="5" width="18" height="7" rx="1"/>
              <rect x="5" y="10" width="10" height="5"/>
            </svg>
            <span>919.555.0187</span>
          </li>
          <li>
            <svg class="contact-icon" viewBox="0 0 20 16" aria-label="Email">
              <rect x="1" y="2" width="18" height="12"/>
              <path d="M1 2 L10 9 L19 2" fill="none" stroke="#070707" stroke-width="1.5"/>
            </svg>
            <span>dwhitfield@taveraenergy.com</span>
          </li>
        </ul>
      </div>
    </section>
  </div>
</body>
</html>
```